Business Cards for a law firm

Business cards for our law firm. Use our silhoette logo and OAK PARTNERS - check our website (www.oakpartners.example)

Contact Information for Business Card

our silhouette logo, OAK PARTNERS, 800-555-0147, Dorian Pemberton, dorian@oakpartners.example

Requirements
Must have
• our silhouette logo, OAK PARTNERS, 800-555-0147, Dorian Pemberton, dorian@oakpartners.example

```html
<!DOCTYPE html>
<html lang="en">
<head>
<meta charset="utf-8">
<title>Oak Partners – Business Cards</title>
<link rel="stylesheet" href="https://fonts.googleapis.com/css2?family=Cinzel:wght@600;700&family=Arimo:wght@400&display=swap">
<style>
  :root {
    --page-bg: #2b2b2d;
    --card-white: #ffffff;
    --navy: #1a2e6b;
    --navy-ink: #1b2a6b;
    --back-dark: #1c1c1e;
    --back-mid: #38383b;
    --silver-light: #f2f2f2;
    --silver-dark: #3a3a3a;
    --text-light: #ffffff;
  }
  * { margin: 0; padding: 0; box-sizing: border-box; }
  html, body {
    width: 1200px; height: 874px; overflow: hidden;
    background: var(--page-bg);
  }
  .canvas { position: relative; width: 1200px; height: 874px; }

  .card {
    position: absolute;
    width: 560px; height: 320px;
    border-radius: 18px;
    overflow: hidden;
    box-shadow: 0 10px 28px rgba(0,0,0,.45);
  }

  /* Back of card */
  .card-back { left: 420px; top: 70px; }
  .back-pattern {
    position: absolute; inset: 0;
    background: linear-gradient(115deg, var(--back-dark) 0%, var(--back-mid) 100%);
  }
  .back-mark {
    position: absolute; right: 62px; bottom: 58px;
    width: 26px; height: 26px;
    background: var(--text-light);
  }

  /* Front of card */
  .card-front { left: 220px; top: 470px; background: var(--card-white); }
  .front-art { position: absolute; inset: 0; }
  .brand {
    position: absolute; left: 34px; top: 60px;
    display: flex; align-items: center; gap: 12px;
  }
  .brand-square { width: 22px; height: 22px; background: var(--navy-ink); }
  .brand-name {
    font-family: "Cinzel", serif; font-weight: 700;
    font-size: 28px; letter-spacing: 2px; color: var(--navy-ink);
  }
  .contact {
    position: absolute; right: 28px; bottom: 24px;
    text-align: right; color: var(--text-light);
  }
  .contact-line {
    display: flex; justify-content: flex-end; align-items: center; gap: 8px;
    font-family: "Arimo", sans-serif; font-size: 15px; line-height: 20px;
  }
  .contact-line svg { width: 13px; height: 13px; fill: var(--text-light); }
  .person-name {
    margin-top: 8px;
    font-family: "Cinzel", serif; font-weight: 700;
    font-size: 24px; letter-spacing: 1px;
  }
</style>
</head>
<body>
<main class="canvas">

  <section class="card card-back" aria-label="Card back">
    <div class="back-pattern" role="img" aria-label="Dark background with a faint repeating pattern of the firm's silhouette emblem"></div>
    <div class="back-mark" aria-hidden="true"></div>
  </section>

  <section class="card card-front" aria-label="Card front">
    <svg class="front-art" viewBox="0 0 560 320" width="560" height="320" aria-hidden="true">
      <defs>
        <linearGradient id="swoosh" x1="0" y1="0" x2="1" y2="0">
          <stop offset="0" stop-color="var(--silver-dark)"/>
          <stop offset=".45" stop-color="var(--silver-light)"/>
          <stop offset=".75" stop-color="var(--silver-dark)"/>
          <stop offset="1" stop-color="var(--silver-light)"/>
        </linearGradient>
      </defs>
      <path d="M0 205 Q 330 300 560 72 L560 320 L0 320 Z" fill="var(--navy)"/>
      <path d="M0 198 Q 330 292 560 64 L560 72 Q 330 300 0 205 Z" fill="url(#swoosh)"/>
    </svg>

    <div class="brand">
      <span class="brand-square" aria-hidden="true"></span>
      <span class="brand-name">OAK PARTNERS</span>
    </div>

    <div class="contact">
      <p class="contact-line">800-555-0147
        <svg viewBox="0 0 24 24"><path d="M6.6 10.8a15 15 0 0 0 6.6 6.6l2.2-2.2a1 1 0 0 1 1-.25 11.4 11.4 0 0 0 3.6.57 1 1 0 0 1 1 1V20a1 1 0 0 1-1 1A17 17 0 0 1 3 4a1 1 0 0 1 1-1h3.5a1 1 0 0 1 1 1c0 1.25.2 2.45.57 3.6a1 1 0 0 1-.25 1z"/></svg>
      </p>
      <p class="contact-line">dorian@oakpartners.example
        <svg viewBox="0 0 24 24"><path d="M2 5h20v14H2z M3 6l9 7 9-7v1.5l-9 7-9-7z" fill-rule="evenodd"/></svg>
      </p>
      <p class="contact-line">www.oakpartners.example
        <svg viewBox="0 0 24 24"><circle cx="12" cy="12" r="10"/></svg>
      </p>
      <p class="person-name">Dorian Pemberton</p>
    </div>
  </section>

</main>
</body>
</html>
```